Quorva - corporate Business Card

We need a good look and innovative business card for a new start up company based in Los Angeles called "Quorva". We are in a payment business, including payment card, app, and ewallet. We are expert in online payment and Card not present (CNP) transaction.
We need an innovative, modern business card.

Our logo font is Aero Matics

Target Market(s)

Startup - Bank - Online Payment - Card Manufacturing

Industry/Entity Type

Startup

Contact Information for Business Card

phone: 555 014 7396 - Address: 4172 Marlowe blvd, Ardenvale, OR 90299

Requirements
Must have
• Message: innovative, professional, expert, high tech, trust, online payment expert, security
Nice to have
• no comment
Should not have
• no Comment

```html
<!DOCTYPE html>
<html lang="en">
<head>
<meta charset="UTF-8">
<title>Quorva — Business Card</title>
<link rel="stylesheet" href="https://fonts.googleapis.com/css2?family=Exo+2:wght@400;500;700&display=swap">
<style>
  :root {
    --brand-red: #b71c2e;
    --brand-red-soft: #c2303f;
    --frost: #f4f2f2;
    --frost-edge: #e6e2e2;
    --canvas-bg: #e9e7e7;
    --ink-light: #ffffff;
  }
  * { box-sizing: border-box; margin: 0; padding: 0; }
  html, body {
    width: 1200px; height: 900px; overflow: hidden;
    background: var(--canvas-bg);
    font-family: "Exo 2", sans-serif;
  }
  .canvas { position: relative; width: 1200px; height: 900px; }

  .card {
    position: absolute;
    width: 556px; height: 345px;
    border-radius: 30px;
    overflow: hidden;
    box-shadow: 0 6px 18px rgba(0,0,0,0.12);
    background: var(--frost);
  }
  .card--front { left: 238px; top: 60px; }
  .card--back  { left: 458px; top: 520px; }

  .card__top {
    position: absolute; left: 0; top: 0; right: 0; height: 162px;
    background: linear-gradient(180deg, #f7f6f6 0%, var(--frost-edge) 100%);
  }
  .card__band {
    position: absolute; left: 0; right: 0; top: 162px; bottom: 0;
    background: var(--brand-red);
  }

  .brand {
    position: absolute; top: 38px;
    display: flex; align-items: center; gap: 12px;
  }
  .card--front .brand { left: 122px; }
  .card--back .brand { left: 120px; flex-direction: row-reverse; }
  .brand__dot {
    width: 94px; height: 94px; border-radius: 50%;
    background: var(--brand-red);
    flex: none;
  }
  .brand__name {
    font-weight: 500; font-size: 58px; line-height: 1;
    color: var(--brand-red); letter-spacing: 2px;
  }
  .card--back .brand__name { transform: scaleX(-1); }

  .contact {
    position: absolute; left: 0; right: 0; top: 162px; bottom: 0;
    color: var(--ink-light); text-align: center;
  }
  .contact__name { position: absolute; left: 0; right: 0; top: 20px; font-weight: 700; font-size: 21px; letter-spacing: 0.3px; }
  .contact__role { position: absolute; left: 0; right: 0; top: 45px; font-size: 17px; }
  .contact__rule {
    position: absolute; left: 203px; width: 150px; top: 75px; height: 1px;
    background: linear-gradient(90deg, transparent, rgba(255,255,255,0.8), transparent);
  }
  .contact__line { position: absolute; left: 0; right: 0; font-size: 15px; letter-spacing: 0.2px; }
  .contact__line--web { top: 89px; }
  .contact__line--address { top: 124px; }
  .contact__divider { display: inline-block; width: 1px; height: 20px; background: var(--ink-light); vertical-align: -4px; margin: 0 7px; }

  .pattern-field {
    position: absolute; left: 0; right: 0; top: 162px; bottom: 0;
    background: linear-gradient(180deg, var(--brand-red) 0%, var(--brand-red-soft) 100%);
  }
</style>
</head>
<body>
<main class="canvas">
  <section class="card card--front" aria-label="Business card front">
    <div class="card__top"></div>
    <div class="card__band"></div>
    <div class="brand">
      <span class="brand__dot"></span>
      <span class="brand__name">quorva</span>
    </div>
    <div class="contact">
      <p class="contact__name">Dorian Kessler</p>
      <p class="contact__role">Director</p>
      <span class="contact__rule"></span>
      <p class="contact__line contact__line--web">555 014 7396<span class="contact__divider"></span>www.quorva.com</p>
      <p class="contact__line contact__line--address">4172 Marlowe blvd, Ardenvale, OR 90299</p>
    </div>
  </section>

  <section class="card card--back" aria-label="Business card back">
    <div class="card__top"></div>
    <div class="pattern-field" role="img" aria-label="Repeating brand-mark pattern on red"></div>
    <div class="brand">
      <span class="brand__dot"></span>
      <span class="brand__name">quorva</span>
    </div>
  </section>
</main>
</body>
</html>
```